Snapnook needs You

Help us create an inviting, amazing, sleek, simple, clear landing page for a picture-memory-social connection site!

Business Name: SnapNook
Industry: Social Networking and Creativity through Pictures
A web platform for and about a community that is driven by a passion for sharing, caring, bonding, collaborating, creating and earning with pictures, through pictures and other related creative activities. This is going to be a great site for all creative artists-photographers, artists, graphic artists to express their work and their creativity.

The main focus of the site is - CONNECTIONS.
This will be uncoded.

Desired Website Screen Size
1024x768... Widescreen/Landscape orientation, is what we mean... So it fits on a CPU screen.

Desired look and feel and message
Look: Visitor should feel immersed in the page, in the world the page creates, simple, elegant, sophisticated, contemporary. We really like a clean uncluttered look.

Special mention: By the way we love the marketing genius who thought up this branding for velu yogurt where they used the two dots above the o to create a branding effect that made this brand instantly identifiable. http://www.velu-dairy.ca/en/

The two dots by themselves without having even the name present brings up the whole brand now. The dots are used above all the ingredients of the yogurt creating friendly figures, and above people in commercials-bringing the people onto the side of "team" velu. Snapnook may have a character created or something distinctive in the letters in the name created to brand the site as well.

Feel: Engaging; Magical without being corny, here is a link to give an example look and feel but please do not be hindered in your creativity by this suggestion. We love all creative angles.
http://artscrapyard.com/graphic/5829317-camera-film-roll-blue-background

Message: Life and memories and connections through pictures.

Target audience:
The site is focused on pictures but not confined to photography enthusiasts (although they are an integral part of the site). Customers/Visitors will include families, corporates and the younger generation - all age groups, all class, everyone with pictures to express, memories to share.

Website design we like:
http://brindlework.com/work/northern-ballet-house/
http://brindlework.com/work/zapverse/

What colors do we want to see on our landing page?
We would like the background to be grey or blue since it is grey is picture neutral colour and blue highlights pictures well and we also like blue and silver, which can be integrated into the theme. Also like green. But please do not let these instructions limit your creativity. We are open to new ideas and colours.

Predetermined Concepts if any:
We have a concept in mind and we think it would be cool to have an interface for the user through the back of a camera on the landing page -This could be used to create a scene or world the visitor feels a part of or is immersed into. The back screen of the camera may act as a screen for the slideshow of featured pictures on the site.

Content on the Page:
Photo Gallery with full screen, thumbnail view, zoom option etc.
Prominent but short introductory message
Sign in / Login Options
Links: Home Page; About; Info/Help; Contact Us; Privacy Policy; Terms of Use
At the bottom of the page: Follow Me/Like/Workplaza...social buttons.

Please feel free to add any other element to the landing page that you think might add to the effect of simple yet amazing look -clean, simple, uncluttered, sophisticated, stylish, inviting and engaging.
The concept is a guideline, but we would like you to be as creative as you can, even if it meant stepping out of these guidelines - rethink design, style, content if you like. We believe in bringing a solution in an innovative yet simple and elegant style. Something a visitor would be intrigued enough to explore and the guest would feel comfortable enough taking that step forward to have fun on the site. If you believe in the same, and you have the skill then you will have what we need. Good luck, go for it and we are excited to see what the amazing designers on this amazing site have to offer.
If you have any questions please free to ask.

HI wanted to send an update that this project design has been guaranteed.

Our site will be one to celebrate and showcase imagination as well as connection.  We would love to see what you create. Keep in mind our site will showcase all creativity, photographs, artists, graphic artists so this would be a benefit you may want to take advantage of in the future, a place where, if you so choose, you could gain exposure for your work. Therefore, even if you do not win the design project there is possible future benefit.

Imagination is everything.
Imagination encircles the world.-Halvorsen

Reason: We are giving the designers who accepted invites but have not yet submitted a chance to finish their submissions and the ones who are working on revisions a chance to finish those:)

Hello everyone,

Due to time constraints we must come to a decision sooner than the deadline of 28th. 

So, please try to submit any new designs or modifications to the old ones before the 26th. We are very thankful to all of you who have participated - for your designs, enthusiasm and kind words. 

Good luck! :)

• Thank you for the interest shown and your submissions! Designers who have submitted up until now have shown great potential. We are VERY excited with the quality of work and designs.

We want to add that Snapnook is not exclusively for the photographers. The site is for every person who may have a picture to store, organise, use or share - whether publicly or with only a few friends and family.

Snapnook is about allowing people to take control of their creativity. It is about providing tools to our users so that they can build their own connections and social network... of friends, family, fans, clients, ideas, thoughts, emotions etc. through pictures without worrying about their privacy or control over their creations.

With this update we want to encourage others to go beyond the camera theme. Do not let us restrict your creativity. Let YOUR OWN ideas take over if that’s what you think will best convey the message and will appeal to the users.

```html
<!DOCTYPE html>
<html lang="en">
<head>
<meta charset="utf-8">
<title>SnapNook — Life. Memories. Connections.</title>
<link rel="stylesheet" href="https://fonts.googleapis.com/css2?family=Lobster&family=Anton&family=Arimo:wght@400;700&display=swap">
<style>
  :root {
    --paper: #cfc4c3;
    --paper-dark: #c2b6b5;
    --teal: #3f7f80;
    --teal-deep: #1f6a6b;
    --teal-ring: #4c8b8c;
    --teal-soft: #7fa9a8;
    --cream: #efe9e6;
    --brown: #5a2e22;
    --clay: #a58a80;
    --clay-dark: #6e4f46;
    --red: #e5484a;
    --footer: #6f6d6c;
    --sky: #6fd2f2;
    --ocean: #1c8bc0;
    --navy: #0b4a78;
    --film: #2c3236;
  }
  * { box-sizing: border-box; margin: 0; padding: 0; }
  html, body { width: 1200px; height: 1054px; overflow: hidden; }
  body {
    position: relative;
    background: radial-gradient(ellipse at 50% 40%, var(--paper) 0%, var(--paper-dark) 100%);
    font-family: "Arimo", Arial, sans-serif;
  }
  .site-header {
    position: absolute; left: 0; top: 0; width: 1200px; height: 100px;
    background: var(--teal);
    border-bottom: 2px solid #8a7a74;
  }
  .brand {
    position: absolute; left: 262px; top: 8px; width: 120px; height: 96px;
    background: var(--cream); border-radius: 8px;
    box-shadow: 2px 4px 8px rgba(0,0,0,.35);
    transform: rotate(-5deg);
    display: flex; align-items: center; justify-content: center; gap: 6px;
    text-decoration: none;
  }
  .brand-dot { width: 12px; height: 12px; background: var(--teal-deep); }
  .brand-name { font-weight: 700; font-size: 19px; color: var(--teal-deep); }
  .account-links { position: absolute; top: 16px; left: 800px; display: flex; gap: 14px; }
  .account-links a { font-family: "Lobster", cursive; font-size: 15px; text-decoration: none; }
  .account-links .login { color: #7fe0dc; border-bottom: 2px solid #2e6b6b; }
  .account-links .signup { color: #f3e6e0; text-shadow: 1px 1px 0 var(--brown); border-bottom: 2px solid var(--brown); }
  .main-nav { position: absolute; top: 66px; left: 556px; display: flex; align-items: center; }
  .main-nav a {
    color: var(--cream); font-size: 11.5px; text-decoration: none;
    padding: 8px 7px; line-height: 14px;
  }
  .main-nav a.current { background: var(--teal-deep); border-radius: 8px; border: 2px solid #2d5e5f; padding: 6px 9px; margin-right: 4px; }

  .vignette {
    position: absolute; border-radius: 50%;
    border: 7px solid var(--teal-ring);
    background:
      radial-gradient(circle at 35% 30%, rgba(239,233,230,.95) 0%, rgba(239,233,230,.6) 40%, rgba(127,169,168,.55) 75%, rgba(31,106,107,.6) 100%),
      var(--cream);
  }
  .vignette-one { left: 270px; top: 155px; width: 218px; height: 218px; }
  .vignette-two { left: 469px; top: 242px; width: 212px; height: 212px; }
  .vignette-three { left: 665px; top: 161px; width: 236px; height: 236px; }

  .word { position: absolute; font-family: "Lobster", cursive; color: var(--teal-deep); text-shadow: 2px 2px 0 var(--cream); transform: rotate(-6deg); white-space: nowrap; }
  .word-life { left: 352px; top: 334px; font-size: 50px; }
  .word-memories { left: 457px; top: 428px; font-size: 50px; }
  .word-connections { left: 672px; top: 350px; font-size: 53px; }
  .tagline { position: absolute; left: 566px; top: 512px; font-family: "Lobster", cursive; font-size: 57px; color: var(--brown); text-shadow: 3px 3px 3px rgba(0,0,0,.3); transform: rotate(-8deg); white-space: nowrap; }

  .feature-shape { position: absolute; left: 0; top: 0; }
  .showcase {
    position: absolute; left: 242px; top: 541px; width: 352px; height: 352px; border-radius: 50%;
    border: 12px solid var(--teal-ring);
    background:
      linear-gradient(180deg, rgba(44,50,54,0) 0%, rgba(44,50,54,0) 58%, rgba(44,50,54,.75) 78%, rgba(180,190,195,.6) 100%),
      radial-gradient(circle at 58% 42%, var(--sky) 0%, var(--ocean) 40%, var(--navy) 100%);
  }
  .upload-button {
    position: absolute; left: 548px; top: 796px; width: 180px; height: 180px; border-radius: 50%;
    background: var(--red); box-shadow: 3px 5px 8px rgba(0,0,0,.35);
    display: flex; align-items: center; justify-content: center; text-align: center;
    text-decoration: none;
  }
  .upload-button::before { content: ""; position: absolute; inset: 8px; border-radius: 50%; border: 2px dotted rgba(255,255,255,.7); }
  .upload-button span { font-family: "Anton", sans-serif; font-size: 40px; line-height: 42px; color: var(--cream); text-shadow: 2px 3px 0 #7a2a2a; transform: rotate(6deg); }

  .site-footer { position: absolute; left: 0; top: 1005px; width: 1200px; height: 49px; background: var(--footer); }
  .site-footer p { position: absolute; left: 258px; top: 14px; color: #eeeeee; font-size: 10px; }
  .social { position: absolute; left: 785px; top: 8px; display: flex; gap: 10px; }
  .social a {
    width: 26px; height: 26px; border-radius: 50%; background: #4d4a48; border: 2px solid #8c8886;
    display: flex; align-items: center; justify-content: center;
  }
  .social svg { display: block; }
</style>
</head>
<body>
  <header class="site-header">
    <a class="brand" href="#"><span class="brand-dot"></span><span class="brand-name">SnapNook</span></a>
    <div class="account-links">
      <a class="login" href="#">Login</a>
      <a class="signup" href="#">Sign Up Now</a>
    </div>
    <nav class="main-nav">
      <a class="current" href="#">Home</a>
      <a href="#">About</a>
      <a href="#">Info</a>
      <a href="#">Contact Us</a>
      <a href="#">Privacy Policy</a>
      <a href="#">Terms of Use</a>
    </nav>
  </header>

  <div class="vignette vignette-one" role="img" aria-label="Retro teal illustration of smiling women"></div>
  <div class="vignette vignette-three" role="img" aria-label="Retro teal illustration of two men in suits"></div>
  <div class="vignette vignette-two" role="img" aria-label="Retro teal illustration of a surprised couple"></div>
  <span class="word word-life">Life.</span>
  <span class="word word-connections">Connections.</span>
  <span class="word word-memories">Memories.</span>

  <svg class="feature-shape" width="1200" height="1054" aria-hidden="true">
    <polygon points="564,622 942,580 856,907" fill="var(--clay)"/>
    <g fill="var(--clay-dark)" stroke="#d8c8c2" stroke-width="2" stroke-dasharray="2 3">
      <circle cx="712" cy="640" r="21"/><circle cx="770" cy="652" r="21"/>
      <circle cx="711" cy="694" r="21"/><circle cx="772" cy="703" r="21"/>
      <circle cx="682" cy="742" r="21"/><circle cx="744" cy="755" r="21"/>
    </g>
    <g fill="none" stroke="#f1e8e4" stroke-width="2">
      <rect x="702" y="632" width="20" height="15"/><polyline points="703,645 709,638 714,643 717,640 721,645"/>
      <rect x="760" y="646" width="20" height="13" rx="2"/><circle cx="770" cy="652" r="4"/>
      <rect x="704" y="687" width="14" height="14"/><path d="M700 690h4M718 698h4M707 683v4M715 701v4"/>
      <circle cx="765" cy="703" r="3"/><circle cx="778" cy="696" r="3"/><circle cx="778" cy="710" r="3"/><path d="M767 702l9-5M767 704l9 5"/>
      <rect x="674" y="740" width="16" height="8"/><rect x="677" y="734" width="10" height="6"/>
      <rect x="735" y="749" width="18" height="13"/><polyline points="735,749 744,756 753,749"/>
    </g>
  </svg>

  <div class="showcase" role="img" aria-label="Blue glowing scene with a film roll and a flame symbol"></div>
  <span class="tagline">through pictures</span>
  <a class="upload-button" href="#"><span>UPLOAD<br>YOURS</span></a>

  <footer class="site-footer">
    <p>snapnook. all righs reserved 2012</p>
    <div class="social">
      <a href="#" aria-label="Social profile"><svg width="8" height="8"><circle cx="4" cy="4" r="3.5" fill="#e6e1de"/></svg></a>
      <a href="#" aria-label="Social feed"><svg width="8" height="8"><circle cx="4" cy="4" r="3.5" fill="#e6e1de"/></svg></a>
      <a href="#" aria-label="News feed"><svg width="12" height="12" fill="none" stroke="#e6e1de" stroke-width="1.8"><circle cx="2" cy="10" r="1.2" fill="#e6e1de" stroke="none"/><path d="M1 6a5 5 0 0 1 5 5M1 2a9 9 0 0 1 9 9"/></svg></a>
      <a href="#" aria-label="Email"><svg width="13" height="10" fill="none" stroke="#e6e1de" stroke-width="1.5"><rect x="0.75" y="0.75" width="11.5" height="8.5"/><polyline points="1,1 6.5,5.5 12,1"/></svg></a>
    </div>
  </footer>
</body>
</html>
```